Business Card - Business Consultancy

Newly Established Company, specializing in Business Consultancy, Human Resource Management, Talent Acquisition and Payroll Solutions.

We need a Business card design which portrays "elegance" and a very sleek yet business-like design. We would like a nice blue trimming (which goes well with the logo) to separate the content of the business card at the top. We would also like to see the design using the color silver either as a background or incorporated into it.

The final design should be a Business card which has colors matching the logo; a nice font; the above-mentioned specifics that adheres to the theme of "a stylish and professional business"

FYI: please do not have too fanciful designs.

Industry/Entity Type

Business Consultant

Contact Information for Business Card

Darren Lim
Business Development Director
Arbor Talent Consulting Private Limited
27 Wexley Street, #05-03B
Harbourgate Trade Building
Singapore 059317
Mobile : (+65) 98354417
Email : dlim@arbortalent-advisory.com
Alternative : arbortalentadvisory@mailbox-example.com

Requirements
Must have
• Nice Blue Trimming matching Logo which separates content, see attached
• Design incorporates either a silver background or the use of the color silver
Should not have
• No Fanciful Designs
• No Childish Designs
• No Overly Complicated Designs

```html
<!DOCTYPE html>
<html lang="en">
<head>
<meta charset="utf-8">
<title>Arbor Talent Consulting – Business Card</title>
<link rel="stylesheet" href="https://fonts.googleapis.com/css2?family=Arimo:wght@400;700&family=Roboto+Mono:wght@700&display=swap">
<style>
  :root {
    --bg-light: #d9d9d9;
    --bg-dark: #8a8a8a;
    --card: #ffffff;
    --ink: #111111;
    --muted: #6b6b6b;
    --brand-blue: #1a7fd1;
    --band: #0d0d0d;
    --silver-light: #f2f3f5;
    --silver: #c7cacf;
    --silver-dark: #a3a7ad;
  }
  * { box-sizing: border-box; margin: 0; padding: 0; }
  html, body { width: 1200px; height: 960px; overflow: hidden; }
  body {
    background: radial-gradient(ellipse at 50% 35%, var(--bg-light), var(--bg-dark));
    font-family: "Arimo", Arial, sans-serif;
    color: var(--ink);
    display: flex;
    align-items: center;
    justify-content: center;
    gap: 40px;
  }
  .card {
    position: relative;
    width: 540px;
    height: 309px;
    background: var(--card);
    box-shadow: 0 10px 30px rgba(0,0,0,.25);
    overflow: hidden;
  }

  /* Front */
  .card--front {
    display: flex; align-items: center; justify-content: center; gap: 18px;
    background: linear-gradient(135deg, var(--silver-light) 0%, #ffffff 45%, var(--silver) 100%);
  }
  .card--front::after {
    content: ""; position: absolute; left: 0; right: 0; bottom: 0; height: 6px;
    background: var(--brand-blue);
  }
  .brand-dot { width: 70px; height: 70px; border-radius: 50%; background: var(--brand-blue); flex: none; }
  .brand-name--large { font-size: 64px; font-weight: 700; color: var(--brand-blue); letter-spacing: 4px; }

  /* Back */
  .brand { position: absolute; left: 34px; top: 40px; display: flex; align-items: center; gap: 12px; }
  .brand .brand-dot { width: 44px; height: 44px; }
  .brand-name { font-size: 36px; font-weight: 700; color: var(--brand-blue); letter-spacing: 2px; }
  .divider { position: absolute; left: 268px; top: 26px; width: 1px; height: 96px; background: var(--silver-dark); }
  .person { position: absolute; right: 30px; top: 56px; text-align: right; }
  .person__name { font-size: 28px; font-weight: 700; }
  .person__title { font-size: 13px; color: var(--muted); margin-top: 4px; }
  .trim {
    position: absolute; left: 34px; right: 30px; top: 134px; height: 3px;
    background: var(--brand-blue);
  }
  .address { position: absolute; left: 34px; top: 152px; font-size: 11.5px; line-height: 1.45; font-style: normal; }
  .address__company { font-weight: 700; }
  .contacts { position: absolute; right: 26px; top: 150px; list-style: none; font-size: 11.5px; }
  .contacts li { display: flex; align-items: center; justify-content: flex-end; gap: 8px; height: 24px; }
  .icon { width: 18px; height: 18px; flex: none; }
  .silver-strip {
    position: absolute; left: 0; right: 0; bottom: 40px; height: 8px;
    background: linear-gradient(90deg, var(--silver-dark), var(--silver-light) 50%, var(--silver-dark));
  }
  .services {
    position: absolute; left: 0; right: 0; bottom: 0; height: 40px;
    background: var(--band); color: #fff;
    font-family: "Roboto Mono", monospace; font-weight: 700; font-size: 12.5px;
    letter-spacing: 2px; display: flex; align-items: center; padding-left: 34px;
    white-space: nowrap;
  }
  .services .sep { color: var(--silver); }
</style>
</head>
<body>
  <section class="card card--front" aria-label="Card front">
    <span class="brand-dot"></span>
    <span class="brand-name--large">ARBOR</span>
  </section>

  <section class="card card--back" aria-label="Card back">
    <div class="brand">
      <span class="brand-dot"></span>
      <span class="brand-name">ARBOR</span>
    </div>
    <div class="divider"></div>
    <div class="person">
      <p class="person__name">Darren Lim</p>
      <p class="person__title">Business Development Director</p>
    </div>
    <div class="trim"></div>
    <address class="address">
      <p class="address__company">Arbor Talent Consulting Pte. Ltd.</p>
      <p>27 Wexley Street, #05-03B</p>
      <p>Harbourgate Trade Building</p>
      <p>Singapore 059317</p>
    </address>
    <ul class="contacts">
      <li>+65 9835-4417
        <svg class="icon" viewBox="0 0 20 20"><circle cx="10" cy="10" r="10" fill="var(--brand-blue)"/><rect x="7" y="4.5" width="6" height="11" rx="1" fill="none" stroke="#fff" stroke-width="1.4"/><circle cx="10" cy="13.2" r=".8" fill="#fff"/></svg>
      </li>
      <li>dlim@arbortalent-advisory.com
        <svg class="icon" viewBox="0 0 20 20"><circle cx="10" cy="10" r="10" fill="var(--brand-blue)"/><rect x="5" y="6.5" width="10" height="7" fill="none" stroke="#fff" stroke-width="1.3"/><path d="M5 6.5l5 4 5-4" fill="none" stroke="#fff" stroke-width="1.3"/></svg>
      </li>
      <li>arbortalentadvisory@mailbox-example.com
        <svg class="icon" viewBox="0 0 20 20"><circle cx="10" cy="10" r="10" fill="var(--brand-blue)"/><rect x="5" y="6.5" width="10" height="7" fill="none" stroke="#fff" stroke-width="1.3"/><path d="M5 6.5l5 4 5-4" fill="none" stroke="#fff" stroke-width="1.3"/></svg>
      </li>
    </ul>
    <div class="silver-strip"></div>
    <div class="services">Recruitment&nbsp;<span class="sep">|</span>&nbsp;HR Solutions&nbsp;<span class="sep">|</span>&nbsp;Business Consultancy</div>
  </section>
</body>
</html>
```